Systems and Technology Consultants - Website

Design & Build a website for a new company which operates in the Systems and Technology space for Transportation, Government and Commercial sectors.

Overall design should be minimalist in nature.
Should also have a feed that provides news and event updates on the main page.
Logo has already been awarded and should be incorporated into the site.

We like the overall layout, functionality and simplicity of the below sites. Submitted designs could be similar to or a combination of the aspects on these sites, or perhaps a whole different concept - we are open to new ideas.
Norvique.com
Teblo.it

Update 1 Dated 27 May 2014

All I am moving away from the Teblo.it website and would like it to be more aligned with Norvique.com not only in layout but in functionality. I will be extending the deadline of this design brief for two weeks to incorporate additional requirements and will add addtional funding to the project.

Apologies for not having more information available to provide but with so many submissions its getting confusing.

Thanks Derek

Please note that the brief has been updated and the deadline has been extended.

Important: We will need two language versions of the website, English and Arabic; the website is hosted on HostPelican

Hello All, Thank you for your submissions. We have narrowed it down to the final 6 designers and I just wanted to take a moment and provide a bit of feedback regarding the concepts that we like and the modifications we are looking for. First, let me mention some of the design functions we like. - At the top of the homepage we really like the "region" or "language" tab so that the website can be viewed in both English and Arabic. - We like the homepage to have clear color variation so that the different sections of the homepage are distinct. Additionally, we like the bottom portion of the homepage to be in red. We feel that draws attention to our contact information. Again, we would like the colors to integrate black, gray-scale, red, etc. - Having a search tab at the top of the home page, or integrated into the main image, so that the site is easy to navigate. - We especially like the main image to have the scrolling tabs at the bottom so it is easy to browse the services offered (Consultancy, Solutions Architecture, Masters Systems Integration, Independent Design Review). - In regards to the services offered tab we really like the idea that a few people presented that have the outside of our logo with an icon in the middle of consultancy, solutions, etc., etc. Secondly, as mentioned in our brief we really enjoy the design of norvique site. Specially, we enjoy the strong iconic images they use, the way the tabs at the top scroll easily, and contact us page that generates an email. Lastly, I've included some photos of the concept we have been working on. What we are trying to demonstrate is how our company offers a range of services that are essentially linked together. We provide individual services that when combined present the full service package. We would like this concept to be integrated into the over concept of our website. Please feel free to ask for clarification of any of the above points or contact us if you have any additional questions. We appreciate all of your hard work and are very excited to see the updated designs. Best, Marta Vennick Quelbrant Senior Program Manager marta.vennick@quelbrant-example.com

Industry/Entity Type

Government

Font styles to use
Serif
Sans Serif

Requirements
Must have
• Must work on/adapt to various/mobile devices (responsive)
Must be simple and straightforward
Colors should be in line/matching with logo
2 language versions: English and Arabic (no Thai)
Services should be the first group/row of items after/below the main image
Note: the website will be hosted by hostpelican
Nice to have
• Submit feedback form
What's New section
The banner at the bottom of the site should not be too large; we would like a narrow one more
It would be nice if the header/top banner (with Home, About, etc. tabs) could stay in place as you scroll down (like Norvique and Chatterloop)
We will likely only use one image with a Company slogan on the Home page rather than a carousel of images to rotate through
Should not have
• This is the existing website: http://www.quelbrant-example.org
We do not like the animation, the way the banner icons/titles bounce
Not simple enough, we don't like the functionality or how pages load so slowly
We do not like the logo centered - it should be at the left
The banner and its tabs should not be towards the right, we would like them to be centered, to go all the way across and to be below the logo

```html
<!DOCTYPE html>
<html lang="en">
<head>
<meta charset="utf-8">
<title>Quelbrant — Systems &amp; Technology Consultants</title>
<link href="https://fonts.googleapis.com/css2?family=Open+Sans:wght@400;600;700&display=swap" rel="stylesheet">
<style>
:root{
  --red:#d40000;
  --red-dark:#b80000;
  --ink:#2b2b2b;
  --muted:#8a8a8a;
  --line:#d6d6d6;
  --band:#f5f5f5;
  --box:#f2f2f2;
  --footer:#262626;
  --footer-bottom:#1b1b1b;
  --footer-text:#b9b9b9;
  --white:#ffffff;
}
*{box-sizing:border-box;margin:0;padding:0}
html,body{width:1200px;height:2163px;overflow:hidden}
body{position:relative;background:var(--white);font-family:"Open Sans",Arial,sans-serif;color:var(--ink)}
a{color:inherit}
.abs{position:absolute}

/* top strip */
.topbar{left:0;top:0;width:1200px;height:120px;background:var(--red)}
.topbar__contact{left:125px;top:25px;display:flex;gap:40px;color:var(--white);font-size:13px}
.topbar__contact span{display:flex;align-items:center;gap:6px}
.topbar__social{left:958px;top:22px;display:flex;gap:9px}
.topbar__social i{display:block;width:14px;height:14px;background:var(--white);border-radius:50%;opacity:.95}

/* header */
.header{left:111px;top:68px;width:978px;height:95px;background:linear-gradient(#ffffff,#ececec);box-shadow:0 1px 3px rgba(0,0,0,.2);z-index:3}
.brand{left:24px;top:14px;display:flex;align-items:center;gap:10px}
.brand__mark{width:22px;height:22px;background:var(--red);border-radius:50%}
.brand__name{font-size:15px;font-weight:700;letter-spacing:2px;color:var(--red)}
.nav{left:362px;top:0;height:95px;display:flex;align-items:center;gap:34px;font-size:13px;color:#7a7a7a}
.nav__item{position:relative;height:95px;display:flex;align-items:center}
.nav__item--active{color:var(--red);font-weight:700}
.nav__item--active::after{content:"";position:absolute;left:-14px;right:-14px;bottom:0;height:3px;background:var(--red)}
.search{left:926px;top:32px;width:32px;height:32px;border-radius:50%;background:#e1e1e1;display:flex;align-items:center;justify-content:center}

/* hero */
.hero{left:0;top:120px;width:1200px;height:464px;background:radial-gradient(ellipse at 55% 45%,#6b6b6b 0%,#3e3e3e 55%,#262626 100%)}
.hero__tag{background:#1c1c1c;color:var(--white);font-size:17px;padding:6px 14px;z-index:2}
.hero__rule{left:0;top:584px;width:1200px;height:4px;background:#e3e3e3}

/* section headings */
.heading{font-size:18px;font-weight:600;color:#333}
.rule{height:0;border-top:1px dotted #c4c4c4}

/* services */
.service{width:290px}
.service__head{display:flex;align-items:center;gap:7px;font-size:17px;font-weight:600;color:#222}
.service__icon{width:34px;height:34px;border-radius:5px;background:var(--red);display:flex;align-items:center;justify-content:center}
.service__text{margin-top:12px;font-size:13px;line-height:16px;color:var(--muted);padding-left:3px}

/* articles */
.articles{left:0;top:1043px;width:1200px;height:337px;background:var(--band)}
.card{width:300px}
.card__media{position:relative;width:300px;height:156px}
.card__caption{position:absolute;left:0;bottom:0;width:100%;height:40px;background:rgba(20,20,20,.82);color:var(--white);font-size:15px;display:flex;align-items:center;padding-left:14px}
.card__text{margin-top:18px;font-size:13px;line-height:22px;color:#555}
.more{font-size:13px;color:var(--red);text-decoration:underline}

/* news + about */
.panel{background:var(--box)}
.news__item{position:absolute;left:14px;width:350px;display:flex;gap:14px}
.news__date{width:36px;text-align:center;color:var(--red);font-size:24px;font-weight:700;line-height:24px}
.news__date small{display:block;font-size:13px;font-weight:400;color:var(--muted);line-height:18px}
.news__title{font-size:14px;font-weight:600;color:#222}
.news__text{margin-top:6px;font-size:12px;line-height:17px;color:var(--muted)}
.about__title{font-size:16px;font-weight:600;color:#222}
.about__text{font-size:12px;line-height:18px;color:var(--muted)}

/* footer */
.footer{left:0;top:1831px;width:1200px;height:284px;background:var(--footer)}
.footer__col{top:74px;color:var(--footer-text)}
.footer__title{display:flex;align-items:center;gap:10px;font-size:15px;color:#dcdcdc}
.footer__title::after{content:"";flex:1;border-top:2px solid #444}
.footer__list{margin-top:24px;font-size:11.5px;line-height:16.5px;list-style:none}
.footer__list--links li{text-decoration:underline}
.footer__body{margin-top:24px;font-size:11.5px;line-height:22px}
.social{display:flex;gap:12px;margin-top:24px}
.social i{display:block;width:32px;height:32px;background:#3a79b8;border-radius:3px}
.subscribe{margin-top:22px;display:flex;height:28px}
.subscribe__field{width:180px;background:#2f2f2f;color:#777;font-size:10px;font-style:italic;display:flex;align-items:center;padding-left:12px}
.subscribe__btn{width:84px;background:var(--red);color:var(--white);font-size:13px;display:flex;align-items:center;justify-content:center}
.bottom{left:0;top:2115px;width:1200px;height:48px;background:var(--footer-bottom);color:#999;font-size:13px}
.totop{left:571px;top:2086px;width:58px;height:58px;border-radius:50%;background:#2c2c2c;display:flex;align-items:center;justify-content:center;z-index:2}
</style>
</head>
<body>

<header>
  <div class="abs topbar">
    <div class="abs topbar__contact">
      <span><svg width="10" height="14" viewBox="0 0 10 14"><rect x="1" y="0.5" width="8" height="13" rx="1.5" fill="none" stroke="#fff" stroke-width="1.4"/><rect x="3" y="10.5" width="4" height="1.2" fill="#fff"/></svg>0800-555-0142-7</span>
      <span><svg width="14" height="10" viewBox="0 0 14 10"><rect x="0.6" y="0.6" width="12.8" height="8.8" fill="none" stroke="#fff" stroke-width="1.2"/><path d="M1 1l6 5 6-5" fill="none" stroke="#fff" stroke-width="1.2"/></svg>contact@quelbrant-example.com</span>
    </div>
    <div class="abs topbar__social"><i></i><i></i><i></i><i></i><i></i><i></i></div>
  </div>

  <div class="abs header">
    <div class="abs brand"><span class="brand__mark"></span><span class="brand__name">QUELBRANT</span></div>
    <nav class="abs nav">
      <span class="nav__item nav__item--active">HOME</span>
      <span class="nav__item">Business Units</span>
      <span class="nav__item">Services</span>
      <span class="nav__item">About Us</span>
      <span class="nav__item">Locations</span>
      <span class="nav__item">Contact Us</span>
    </nav>
    <div class="abs search"><svg width="14" height="14" viewBox="0 0 14 14"><circle cx="6" cy="6" r="4.2" fill="none" stroke="#888" stroke-width="1.8"/><path d="M9 9l4 4" stroke="#888" stroke-width="1.8"/></svg></div>
  </div>
</header>

<section>
  <div class="abs hero" role="img" aria-label="Businessman seen from behind facing a chalkboard wall of hand-drawn business sketches and charts"></div>
  <span class="abs hero__tag" style="left:183px;top:231px">Consulting</span>
  <span class="abs hero__tag" style="left:927px;top:211px">Engineering</span>
  <span class="abs hero__tag" style="left:981px;top:422px">Operations</span>
  <span class="abs hero__tag" style="left:243px;top:461px">Construction</span>
  <span class="abs hero__tag" style="left:857px;top:496px">Maintenance</span>
  <div class="abs hero__rule"></div>
</section>

<section>
  <h2 class="abs heading" style="left:112px;top:648px">What We Do</h2>
  <div class="abs rule" style="left:112px;top:678px;width:977px"></div>

  <div class="abs service" style="left:111px;top:707px">
    <div class="service__head"><span class="service__icon"><svg width="20" height="20" viewBox="0 0 20 20"><circle cx="10" cy="10" r="6" fill="none" stroke="#fff" stroke-width="3" stroke-dasharray="3 2"/><circle cx="10" cy="10" r="2.5" fill="#fff"/></svg></span>Consulting</div>
    <p class="service__text">It is a long established fact that a reader will be distracted by the readable content of a page when looking at its layout.</p>
  </div>
  <div class="abs service" style="left:460px;top:707px">
    <div class="service__head"><span class="service__icon"><svg width="20" height="20" viewBox="0 0 20 20"><circle cx="10" cy="6" r="4" fill="#fff"/><path d="M3 19c0-5 3-8 7-8s7 3 7 8z" fill="#fff"/></svg></span>Engineering</div>
    <p class="service__text">It is a long established fact that a reader will be distracted by the readable content of a page when looking at its layout.</p>
  </div>
  <div class="abs service" style="left:808px;top:707px">
    <div class="service__head"><span class="service__icon"><svg width="20" height="20" viewBox="0 0 20 20"><path d="M3 17h14M5 17V8l6-5 4 6" fill="none" stroke="#fff" stroke-width="2.2"/></svg></span>Construction</div>
    <p class="service__text">It is a long established fact that a reader will be distracted by the readable content of a page when looking at its layout.</p>
  </div>
  <div class="abs service" style="left:111px;top:849px">
    <div class="service__head"><span class="service__icon"><svg width="20" height="20" viewBox="0 0 20 20"><circle cx="10" cy="10" r="7" fill="none" stroke="#fff" stroke-width="2.4"/><path d="M10 5v5l3 3" stroke="#fff" stroke-width="2" fill="none"/></svg></span>Operations</div>
    <p class="service__text">It is a long established fact that a reader will be distracted by the readable content of a page when looking at its layout.</p>
  </div>
  <div class="abs service" style="left:460px;top:849px">
    <div class="service__head"><span class="service__icon"><svg width="20" height="20" viewBox="0 0 20 20"><path d="M3 12a7 7 0 0 1 14 0z" fill="#fff"/><rect x="2" y="13" width="16" height="3" fill="#fff"/></svg></span>Maintenance</div>
    <p class="service__text">It is a long established fact that a reader will be distracted by the readable content of a page when looking at its layout.</p>
  </div>
  <div class="abs service" style="left:808px;top:849px">
    <div class="service__head"><span class="service__icon"><svg width="22" height="20" viewBox="0 0 22 20"><path d="M1 10c4-6 16-6 20 0-4 6-16 6-20 0z" fill="#fff"/><circle cx="11" cy="10" r="3.4" fill="#d40000"/></svg></span>Our Vision</div>
    <p class="service__text">It is a long established fact that a reader will be distracted by the readable content of a page when looking at its layout.</p>
  </div>
</section>

<section>
  <h2 class="abs heading" style="left:112px;top:1010px">Our Articles</h2>
  <div class="abs articles"></div>

  <article class="abs card" style="left:110px;top:1068px">
    <div class="card__media" role="img" aria-label="Businessman in front of a chalkboard of business sketches" style="background:linear-gradient(135deg,#5a5a5a,#2e2e2e)"><span class="card__caption">Lorem lipsum</span></div>
    <p class="card__text">Fusce mauris dapibus, tellus cursus ac commodo, tortor condimentum nibh, ut fermentum massa justo sit amet. Vivamus sagittis lacus...</p>
    <a class="more">Read More</a>
  </article>
  <article class="abs card" style="left:450px;top:1068px">
    <div class="card__media" role="img" aria-label="Notebook, pencil and pen lying on printed financial charts" style="background:linear-gradient(135deg,#e8e8ee,#b9bccb)"><span class="card__caption">Lorem lipsum</span></div>
    <p class="card__text">Fusce mauris dapibus, tellus cursus ac commodo, tortor condimentum nibh, ut fermentum massa justo sit amet. Vivamus sagittis lacus...</p>
    <a class="more">Read More</a>
  </article>
  <article class="abs card" style="left:790px;top:1068px">
    <div class="card__media" role="img" aria-label="Businessman holding an umbrella against a wall with a chalk drawing" style="background:linear-gradient(135deg,#d4d4d4,#8a8a8a)"><span class="card__caption">Lorem lipsum</span></div>
    <p class="card__text">Fusce mauris dapibus, tellus cursus ac commodo, tortor condimentum nibh, ut fermentum massa justo sit amet. Vivamus sagittis lacus...</p>
    <a class="more">Read More</a>
  </article>
</section>

<section>
  <h2 class="abs heading" style="left:110px;top:1426px">Our News</h2>
  <div class="abs rule" style="left:110px;top:1457px;width:379px"></div>
  <h2 class="abs heading" style="left:536px;top:1426px">About Us</h2>
  <div class="abs rule" style="left:532px;top:1457px;width:557px"></div>

  <div class="abs panel" style="left:110px;top:1491px;width:379px;height:306px">
    <div class="news__item" style="top:21px">
      <div class="news__date">27<small>FEB</small></div>
      <div><h3 class="news__title">Lorem lipsum is a simply text</h3><p class="news__text">It is a long established fact that a reader will be distracted by the readable content of a page when looking at its layout.</p></div>
    </div>
    <div class="news__item" style="top:112px">
      <div class="news__date">30<small>FEB</small></div>
      <div><h3 class="news__title">Lorem lipsum is a simply text</h3><p class="news__text">It is a long established fact that a reader will be distracted by the readable content of a page when looking at its layout.</p></div>
    </div>
    <div class="news__item" style="top:208px">
      <div class="news__date">30<small>FEB</small></div>
      <div><h3 class="news__title">Lorem lipsum is a simply text</h3><p class="news__text">It is a long established fact that a reader will be distracted by the readable content of a page when looking at its layout.</p></div>
    </div>
  </div>

  <div class="abs panel" style="left:532px;top:1491px;width:557px;height:306px">
    <div class="abs" role="img" aria-label="Businessman drawing a rising bar chart on a screen" style="left:16px;top:17px;width:199px;height:147px;background:linear-gradient(135deg,#1d3f6e,#0c1a33)"></div>
    <h3 class="abs about__title" style="left:228px;top:14px">Lorem Lipsum</h3>
    <p class="abs about__text" style="left:228px;top:42px;width:315px">It is a long established fact that a reader will be distracted by the readable content of a page when looking at its layout.It is a long established fact that a reader will be distracted by the readable content of a page when looking at its layout.</p>
    <p class="abs about__text" style="left:16px;top:186px;width:525px">It is a long established fact that a reader will be distracted by the readable content of a page when looking at its layout.It is a long established fact that a reader will be distracted by the readable content of a page when looking at its layout.</p>
    <a class="abs more" style="left:16px;top:251px">Read More</a>
  </div>
</section>

<footer>
  <div class="abs footer">
    <div class="abs footer__col" style="left:130px;width:155px">
      <h4 class="footer__title">Contact Info</h4>
      <ul class="footer__list footer__list--links" style="line-height:20px">
        <li>lorem ipsum</li><li>dolor sit amet 106</li><li>1404 consecteture</li><li>adipisicing elit</li>
        <li>eMail: info@quelbrant-example.com</li><li>Phone: 1-800-555-0199</li>
      </ul>
    </div>
    <div class="abs footer__col" style="left:335px;width:210px">
      <h4 class="footer__title">About Us</h4>
      <p class="footer__body">Lorem ipsum dolor sit amet, consectetur adipisicing elit, sed do eiusmod tempor incididunt ut labore et dolore magna aliqua. Ut enim ad minim veniam.</p>
    </div>
    <div class="abs footer__col" style="left:594px;width:155px">
      <h4 class="footer__title">Company Info</h4>
      <ul class="footer__list" style="color:#e0e0e0">
        <li>Home</li><li>Business Units</li><li>Services</li><li>About Us</li><li>Locations</li><li>Contact Us</li>
      </ul>
    </div>
    <div class="abs footer__col" style="left:799px;width:266px">
      <h4 class="footer__title">Stay updates on our Socail Network</h4>
      <div class="social"><i></i><i style="background:#4aa3df"></i><i style="background:#1f74b4"></i></div>
      <h4 class="footer__title" style="margin-top:18px">Join Our Newsletter</h4>
      <div class="subscribe"><span class="subscribe__field">Enter your email address</span><span class="subscribe__btn">Subscribe</span></div>
    </div>
  </div>
  <div class="abs totop"><svg width="18" height="10" viewBox="0 0 18 10"><path d="M1 9l8-7 8 7" fill="none" stroke="#555" stroke-width="1.6"/></svg></div>
  <div class="abs bottom">
    <span class="abs" style="left:130px;top:15px">© Copyrights 2014 All rights Reserved</span>
    <span class="abs" style="left:893px;top:15px">Privacy Policy &amp; Terms of uses</span>
  </div>
</footer>

</body>
</html>
```